Medical VIP club - small design

Please read the specs in a design brief attached. Also we don't have logo in a Vector format and attaching the only version we have.

Club

```html
<!DOCTYPE html>
<html lang="en">
<head>
<meta charset="utf-8">
<title>Verantis — Packages &amp; Prices</title>
<link rel="stylesheet" href="https://fonts.googleapis.com/css2?family=Cinzel:wght@400;600&display=swap">
<style>
  :root {
    --brown-deep: #4a392b;
    --brown-header: #4b3b2d;
    --brown-wave: #56432f;
    --panel: rgba(118, 93, 62, 0.86);
    --rule-dark: #3b2b1e;
    --rule-light: #d9c9ae;
    --text-cream: #d9ccb6;
    --text-active: #a68f6c;
    --title: #e2d6c2;
    --photo-dark: #2c2724;
    --photo-mid: #4d4540;
    --photo-warm: #6a5a4c;
  }
  * { box-sizing: border-box; margin: 0; padding: 0; }
  html, body { width: 1200px; height: 900px; overflow: hidden; background: var(--brown-deep); }
  .page { position: relative; width: 1200px; height: 900px; font-family: "Cinzel", "Times New Roman", serif; }

  .scene { position: absolute; left: 0; top: 170px; width: 1200px; height: 557px;
    background: linear-gradient(90deg, var(--photo-dark) 0%, var(--photo-mid) 30%, var(--photo-warm) 55%, var(--photo-mid) 78%, #3a3440 100%); }
  .scene-glow { position: absolute; left: 0; bottom: 0; width: 1200px; height: 90px;
    background: linear-gradient(180deg, transparent, rgba(200,190,210,0.25)); }

  .header { position: absolute; left: 0; top: 0; width: 1200px; height: 240px; }
  .header svg { display: block; }
  .watermark { position: absolute; left: 380px; top: 20px; font-size: 150px; font-weight: 400;
    color: rgba(255,240,220,0.05); letter-spacing: 4px; line-height: 1; }

  .nav { position: absolute; left: 0; top: 128px; width: 1200px; height: 26px; list-style: none; }
  .nav li { position: absolute; top: 0; font-size: 17px; letter-spacing: 1.6px; color: var(--text-cream); white-space: nowrap; }
  .nav li.is-active { color: var(--text-active); }
  .nav-flourish { position: absolute; left: 786px; top: 104px; width: 186px; height: 68px;
    border-radius: 50%; background: rgba(170,140,100,0.12); }

  .packages { position: absolute; left: 207px; top: 253px; width: 795px; height: 437px;
    background: var(--panel); box-shadow: 0 6px 18px rgba(0,0,0,0.35); }
  .package-title { position: absolute; top: 34px; width: 200px; text-align: center;
    font-size: 16px; font-weight: 600; letter-spacing: 2px; color: var(--title); }
  .title-rule { position: absolute; top: 57px; width: 134px; height: 2px; background: var(--rule-dark); }
  .title-ornament { position: absolute; top: 60px; width: 76px; height: 26px; border-radius: 50% / 0 0 100% 100%;
    background: rgba(60,42,28,0.45); }
  .row-rule { position: absolute; left: 3px; width: 789px; height: 2px; background: var(--rule-dark); }
  .col-rule { position: absolute; top: 3px; width: 1px; height: 330px; background: var(--rule-light); }
  .col-end { position: absolute; top: 328px; width: 9px; height: 9px; border-radius: 50%; background: var(--rule-light); }
  .panel-brand { position: absolute; left: 0; top: 396px; width: 795px; text-align: center;
    font-size: 20px; color: rgba(60,42,28,0.6); letter-spacing: 1px; }

  .footer-links { position: absolute; top: 790px; left: 0; list-style: none; }
  .footer-links li { position: absolute; height: 56px; box-shadow: 0 3px 8px rgba(0,0,0,0.4); }
  .thumb-emergency { left: 79px; width: 90px; background: linear-gradient(90deg, #2a2420, #6b5a48); }
  .thumb-travel { left: 196px; width: 91px; background: linear-gradient(180deg, #d9c7a8, #7a6650); }
  .thumb-service { left: 320px; width: 90px; background: linear-gradient(90deg, #3a2e24, #8a7458 55%, #3a2e24); }
  .thumb-team { left: 437px; width: 93px; background: linear-gradient(90deg, #9c8a70, #e6d9c0 50%, #9c8a70); }
  .thumb-partners { left: 558px; width: 90px; background: linear-gradient(135deg, #3a2d22, #8b765a 50%, #3a2d22); }

  .footer-brand { position: absolute; left: 770px; top: 798px; width: 205px; text-align: center;
    font-size: 32px; color: #a48a68; letter-spacing: 1px; }

  .social { position: absolute; top: 850px; left: 0; list-style: none; }
  .social li { position: absolute; width: 27px; height: 27px; border-radius: 5px;
    background: linear-gradient(180deg, #a99d8e, #7a6f63); }
</style>
</head>
<body>
<main class="page">
  <div class="scene" role="img" aria-label="Photograph of a dimly lit luxury spa interior with stone walls and soft lighting">
    <div class="scene-glow"></div>
  </div>

  <header class="header">
    <svg width="1200" height="240" viewBox="0 0 1200 240" aria-hidden="true">
      <path d="M0 0 H1200 V170 C1000 168 880 150 720 190 C560 232 420 240 230 205 C130 188 60 180 0 178 Z" fill="var(--brown-header)"/>
      <path d="M0 0 H1200 V6 C900 30 600 34 300 12 C180 4 80 0 0 4 Z" fill="var(--brown-wave)"/>
    </svg>
    <div class="watermark" aria-hidden="true">Verantis</div>
  </header>

  <div class="nav-flourish" role="img" aria-label="Decorative swirl ornament framing the registration link"></div>
  <ul class="nav">
    <li style="left:40px">About Us</li>
    <li style="left:205px">VIP Club</li>
    <li class="is-active" style="left:368px">Services</li>
    <li style="left:528px">Packages &amp; Prices</li>
    <li style="left:801px">Registration</li>
    <li style="left:1034px">Contact</li>
  </ul>

  <section class="packages">
    <h2 class="package-title" style="left:28px">Package 1</h2>
    <h2 class="package-title" style="left:296px">Package 2</h2>
    <h2 class="package-title" style="left:552px">Package 3</h2>
    <span class="title-rule" style="left:62px"></span>
    <span class="title-rule" style="left:330px"></span>
    <span class="title-rule" style="left:585px"></span>
    <span class="title-ornament" role="img" aria-label="Ornament" style="left:91px"></span>
    <span class="title-ornament" role="img" aria-label="Ornament" style="left:358px"></span>
    <span class="title-ornament" role="img" aria-label="Ornament" style="left:614px"></span>

    <span class="row-rule" style="top:128px"></span>
    <span class="row-rule" style="top:178px"></span>
    <span class="row-rule" style="top:229px"></span>
    <span class="row-rule" style="top:279px"></span>
    <span class="row-rule" style="top:329px"></span>

    <span class="col-rule" style="left:264px"></span>
    <span class="col-rule" style="left:530px"></span>
    <span class="col-end" style="left:260px"></span>
    <span class="col-end" style="left:526px"></span>

    <div class="panel-brand">Verantis</div>
  </section>

  <ul class="footer-links">
    <li class="thumb-emergency" role="img" aria-label="Photo of an emergency department sign"></li>
    <li class="thumb-travel" role="img" aria-label="Photo of an airplane at an airport"></li>
    <li class="thumb-service" role="img" aria-label="Photo of a hotel reception bell"></li>
    <li class="thumb-team" role="img" aria-label="Photo of the medical team"></li>
    <li class="thumb-partners" role="img" aria-label="Photo of a handshake"></li>
  </ul>

  <div class="footer-brand">Verantis</div>

  <ul class="social" aria-label="Social links">
    <li style="left:1073px"></li>
    <li style="left:1110px"></li>
    <li style="left:1147px"></li>
  </ul>
</main>
</body>
</html>
```